The Quiet Harbor Podcast Cover Art

I'm upgrading my podcast cover art to a new design. The show is called The Quiet Harbor and we interview guests who have gone through different challenges/adversities that we face in life. During the interview, we unpack how they've gotten past the adversity and how that insight might help others. I will link the show and old cover art. I will upload a new photo or two that can be used for the new cover art.

Look at previous cover for items that needed on the cover like Lyrabox, tunewell etc.

Should also have a small caption that states
“UNTOLD STORIES OF EVERYDAY ADVERSITY & PERSEVERANCE”

Tunewell: https://play.tunewellaudio.net/show/8PR4n2GbtqWxLoHvFNZCa7?si=qe3Lx8WbVm-D52KrPhtzRa

Target Market(s)

Podcast learning community

Industry/Entity Type

Podcast, Education

Colors
EB3D1F
EC4F4E
F09395
F8D3D4
FCEDEE

Requirements
Must have
• RM Logo, Colors are red, black and white.

```html
<!DOCTYPE html>
<html lang="en">
<head>
<meta charset="utf-8">
<title>The Quiet Harbor – Podcast Cover</title>
<link href="https://fonts.googleapis.com/css2?family=Anton&family=Oswald:wght@300;400;600&family=Yellowtail&display=swap" rel="stylesheet">
<style>
  :root {
    --stage: #e9e9ec;
    --cover-dark: #2a292c;
    --red: #eb3d1f;
    --band-red: #e8141a;
    --coral: #ec4f4e;
    --pink: #f09395;
    --blush: #f8d3d4;
    --gold: #f8c25a;
    --white: #ffffff;
    --ink: #1b1b1d;
    --dot-green: #2fae4e;
  }
  * { margin: 0; padding: 0; box-sizing: border-box; }
  html, body {
    width: 1200px; height: 675px; overflow: hidden;
    background: var(--stage);
  }
  .stage {
    width: 1200px; height: 675px;
    display: flex; align-items: center; justify-content: center;
  }
  .cover {
    position: relative;
    width: 620px; height: 620px;
    background: var(--cover-dark);
    overflow: hidden;
    box-shadow: 0 10px 30px rgba(0,0,0,.25);
  }
  .accent-field {
    position: absolute;
    right: 0; top: 0;
    width: 330px; height: 330px;
    background: radial-gradient(ellipse at 100% 0%, var(--gold) 0%, var(--pink) 30%, var(--coral) 55%, rgba(232,20,26,.85) 72%, rgba(42,41,44,0) 100%);
  }
  .host-photo {
    position: absolute;
    left: 345px; top: 75px;
    width: 245px; height: 545px;
    border-radius: 120px 120px 0 0;
    background: linear-gradient(180deg, #5a4c66 0%, #4a3f58 38%, #e9e6ea 56%, #f4f2f3 100%);
  }
  .brand-mark {
    position: absolute; right: 16px; top: 92px;
    display: flex; align-items: center; gap: 6px;
    font-family: "Oswald", sans-serif; font-weight: 600;
    font-size: 12px; letter-spacing: 1px; color: var(--ink);
  }
  .brand-mark .square { width: 12px; height: 12px; background: var(--ink); flex: none; }
  .show-title {
    position: absolute; left: 40px; top: 66px;
    font-family: "Anton", sans-serif;
    color: var(--white);
    line-height: .98;
    font-size: 84px;
    text-transform: uppercase;
    transform: skewX(-10deg);
    transform-origin: left bottom;
  }
  .show-title span { display: block; }
  .host-line {
    position: absolute; left: 36px; top: 372px;
    width: 300px;
    white-space: nowrap;
    font-family: "Yellowtail", cursive;
    color: var(--white);
    font-size: 34px;
    line-height: 1;
  }
  .tagline-band {
    position: absolute; left: 0; top: 463px;
    width: 380px; height: 64px;
    background: linear-gradient(90deg, var(--band-red) 0%, #d9131a 70%, rgba(217,19,26,0) 100%);
    display: flex; align-items: center;
    padding-left: 32px;
  }
  .tagline-band::before {
    content: ""; position: absolute; left: 32px; top: 12px;
    width: 3px; height: 40px; background: var(--white);
  }
  .tagline {
    margin-left: 14px;
    font-family: "Oswald", sans-serif; font-weight: 300;
    font-size: 19px; line-height: 1.25; color: var(--white);
    letter-spacing: .2px;
  }
  .listen-links {
    position: absolute; left: 28px; top: 556px;
    display: flex; gap: 8px;
  }
  .listen-pill {
    width: 127px; height: 46px;
    background: var(--white); border-radius: 23px;
    display: flex; align-items: center; gap: 7px;
    padding-left: 14px;
    text-decoration: none; color: var(--ink);
  }
  .listen-pill .dot { width: 22px; height: 22px; border-radius: 50%; background: var(--ink); flex: none; }
  .listen-pill.tunewell .dot { background: var(--dot-green); }
  .listen-pill .label { display: flex; flex-direction: column; font-family: "Oswald", sans-serif; }
  .listen-pill .small { font-size: 8px; font-weight: 400; line-height: 1; }
  .listen-pill .name { font-size: 17px; font-weight: 600; line-height: 1.05; }
</style>
</head>
<body>
<main class="stage">
  <section class="cover" aria-label="The Quiet Harbor podcast cover">
    <div class="accent-field" role="img" aria-label="Decorative warm red, pink and gold background graphic"></div>

    <div class="host-photo" role="img" aria-label="Photo of the host in a blazer and white T-shirt"></div>

    <div class="brand-mark"><span class="square"></span>ROWAN MERCER</div>

    <h1 class="show-title"><span>The</span><span>Quiet</span><span>Harbor</span></h1>
    <p class="host-line">with Rowan Mercer</p>

    <div class="tagline-band">
      <p class="tagline">UNTOLD STORIES OF EVERYDAY<br>ADVERSITY &amp; PERSEVERANCE</p>
    </div>

    <nav class="listen-links">
      <a class="listen-pill tunewell" href="https://play.tunewellaudio.net/show/8PR4n2GbtqWxLoHvFNZCa7?si=qe3Lx8WbVm-D52KrPhtzRa">
        <span class="dot"></span>
        <span class="label"><span class="small">Listen On</span><span class="name">Tunewell</span></span>
      </a>
      <a class="listen-pill lyrabox" href="#">
        <span class="dot"></span>
        <span class="label"><span class="small">Listen On</span><span class="name">Lyrabox</span></span>
      </a>
    </nav>
  </section>
</main>
</body>
</html>
```